Existing Website Requiring new Pages

I have an existing word press website that was built using elementor.
Website: www.tallowcrestcare.com.au
I require the Vacancies page (https://www.tallowcrestcare.com.au/vacancies/) to be modified to display our new properties along with minor tweaks to how the information is presented.
The vacancies to be displayed are the exactly the same as those that are located on the homepage of QMR website (https://qmr.org.au/)
The new pages that link off the Vacancies tab will require custom design.
There are roughly 8 pages/properties to be incorporated. i wish for the design to be very similar to that displayed in the following link; https://www.polunda.com.au/vacancies/merrylands
Along with this the back end has not been updated for the last 3 years so it also requires some maintenance.
Website is in the disability industry and the custom pages will display information relative to Property Vacancies.
I have attached a ZIP file with some design guides, the information for each of the properties (which will need to be modified to show our business name Tallowcrest Care) and the example of how it is to look based off the Polunda website.
If you guys have any suggestions or ideas on how to make this more presentable or possible i'm open to your ideas.
Target Market(s)
People looking for SDA properties custom built for people with a disability
Industry/Entity Type
Disability
Coding
Coded - Design and coding required
Number of Pages Required
5+ page

```html
<!DOCTYPE html>
<html lang="en">
<head>
<meta charset="utf-8">
<title>Vacancies – Tallowcrest Care</title>
<link rel="stylesheet" href="https://fonts.googleapis.com/css2?family=Montserrat:wght@400;500;600;700;800&display=swap">
<style>
:root{
  --orange:#f8b457;
  --nav-active:#f0875a;
  --teal:#40dcc2;
  --pink:#e0168a;
  --ink:#161616;
  --muted:#8c8c8c;
  --line:#e6e6e6;
  --footer-bar:#222326;
  --white:#ffffff;
}
*{box-sizing:border-box;margin:0;padding:0}
html,body{width:1200px;height:3238px;overflow:hidden;background:var(--white);font-family:"Montserrat",sans-serif;color:var(--ink)}
.page{position:relative;width:1200px;height:3238px}

/* header */
.site-header{position:absolute;top:0;left:0;width:1200px;height:122px;background:var(--white)}
.brand{position:absolute;left:112px;top:10px;width:140px;height:96px;display:flex;flex-direction:column;align-items:center;justify-content:flex-end}
.brand-mark{width:46px;height:46px;border-radius:50%;background:#f3a9d4;margin-bottom:8px}
.brand-name{font-size:15px;font-weight:500;color:#4a4a4a;letter-spacing:.3px;text-align:center;line-height:1.05;white-space:nowrap}
.main-nav{position:absolute;top:51px;right:141px;display:flex;gap:23px;font-size:10px;font-weight:700;letter-spacing:.6px}
.main-nav a{color:#3b3b3b;text-decoration:none}
.main-nav a.active{color:var(--nav-active)}

/* hero */
.hero{position:absolute;top:122px;left:0;width:1200px;height:486px;overflow:hidden}
.hero-photo{position:absolute;inset:0;background:linear-gradient(100deg,#9a6a4e 0%,#a27059 35%,#c8a060 55%,#8d8d8a 75%,#6e6e6c 100%)}
.hero-shape{position:absolute;inset:0}
.hero-title{position:absolute;left:94px;top:163px;font-size:54px;font-weight:800;letter-spacing:-.5px}
.hero-sub{position:absolute;left:97px;top:240px;font-size:23px;font-weight:600;line-height:30px}

.teal-band{position:absolute;top:608px;left:0;width:1200px;height:171px;background:var(--teal)}

.search-panel{position:absolute;top:572px;left:172px;width:858px;height:118px;background:var(--white);box-shadow:0 8px 22px rgba(0,0,0,.12)}
.search-field{position:absolute;top:27px}
.search-field label{display:block;font-size:9.5px;font-weight:600;margin-bottom:11px;letter-spacing:.2px}
.select{position:relative;height:36px;border:1px solid #dcdcdc;font-size:10px;color:#8a8a8a;padding:12px 15px}
.select svg{position:absolute;right:11px;top:11px}
.go-btn{position:absolute;left:751px;top:51px;width:65px;height:36px;background:var(--orange);color:var(--white);font-size:12px;font-weight:500;display:flex;align-items:center;justify-content:center;border-radius:2px}

/* map */
.map{position:absolute;left:94px;top:847px;width:1012px;height:354px;border-radius:10px;background:linear-gradient(135deg,#eef1ee 0%,#e6ebe6 55%,#cfe4f0 80%,#bcd9ee 100%)}

/* listing intro */
.eyebrow{position:absolute;left:97px;top:1241px;font-size:12px;font-weight:500;color:var(--orange);letter-spacing:.3px}
.section-title{position:absolute;left:97px;top:1264px;font-size:38px;font-weight:700;line-height:42px;letter-spacing:-.3px}

/* cards */
.listing-grid{position:absolute;left:94px;top:1410px;display:grid;grid-template-columns:repeat(3,296px);column-gap:62px;row-gap:45px}
.property-card{position:relative;width:296px;height:409px;background:var(--white);box-shadow:0 2px 12px rgba(0,0,0,.08)}
.property-card.is-active{border-bottom:3px solid var(--pink)}
.card-photo{position:relative;height:221px;background:linear-gradient(180deg,#5a86c9 0%,#8fb0da 28%,#9b8f87 45%,#6f625a 75%,#7c7c78 100%)}
.card-photo.interior{background:linear-gradient(180deg,#ececec 0%,#dedede 40%,#a9c7b5 60%,#c7b096 100%)}
.card-photo.cloudy{background:linear-gradient(180deg,#9cb8de 0%,#d7e1ef 30%,#4a4c52 50%,#585a5e 80%,#a8a6a1 100%)}
.fav{position:absolute;left:13px;top:13px;width:16px;height:16px;border-radius:50%;background:var(--orange)}
.featured{position:absolute;right:15px;top:17px;background:var(--teal);color:var(--white);font-size:6.5px;font-weight:700;padding:3px 7px;border-radius:8px;letter-spacing:.3px}
.gallery{position:absolute;right:29px;bottom:-9px;width:28px;height:28px;border-radius:50%;background:var(--white);display:flex;align-items:center;justify-content:center}
.gallery-count{position:absolute;right:23px;bottom:11px;width:13px;height:13px;border-radius:50%;background:#111;color:var(--white);font-size:6px;font-weight:700;display:flex;align-items:center;justify-content:center}
.slide-arrow{position:absolute;top:111px;width:20px;height:20px;border-radius:50%;background:rgba(40,40,40,.55)}
.slide-arrow.prev{left:10px}.slide-arrow.next{right:10px}
.card-body{position:absolute;left:0;top:221px;right:0;bottom:0;padding:22px 12px 0 22px}
.status{display:inline-block;font-size:6px;font-weight:700;background:#efefef;padding:3px 6px;border-radius:6px;letter-spacing:.2px}
.card-title{font-size:17px;font-weight:600;margin-top:12px;letter-spacing:-.35px;white-space:nowrap}
.card-loc{font-size:11px;color:var(--muted);margin-top:4px;display:flex;align-items:center;gap:4px}
.card-spec{position:absolute;left:22px;right:18px;top:104px;font-size:9.5px;color:var(--muted);line-height:13px;letter-spacing:.1px}
.card-spec.two-line{top:97px}
.details-btn{position:absolute;left:22px;top:131px;display:flex;align-items:center;justify-content:center;width:104px;height:30px;background:var(--orange);color:var(--white);font-size:10.5px;font-weight:500;border-radius:2px}

/* footer */
.site-footer{position:absolute;top:2871px;left:0;width:1200px;height:297px;border-top:1px solid #eeeeee}
.footer-brand{position:absolute;left:84px;top:48px;width:170px;height:142px;display:flex;flex-direction:column;align-items:center;justify-content:flex-end}
.footer-brand .brand-mark{width:64px;height:64px;margin-bottom:12px}
.footer-brand .brand-name{font-size:20px}
.contact-list{position:absolute;left:94px;top:206px;list-style:none;font-size:12.5px;color:var(--muted);line-height:22.5px}
.contact-list li{display:flex;align-items:center;gap:8px}
.social{position:absolute;left:517px;top:57px;display:flex;flex-direction:column;gap:10px}
.social span{width:33px;height:33px;border-radius:50%;background:#3c5aa6}
.social span.badge{background:#6b2d8a}
.social span.dark{background:#1b1b1b}
.social span.blue{background:#1d76b5}
.footer-col{position:absolute;top:48px;width:234px}
.footer-col h3{font-size:13.5px;font-weight:500;letter-spacing:.3px;border-left:2px solid #3aa8f0;padding-left:14px;line-height:16px;margin-bottom:18px}
.footer-col ul{list-style:none}
.footer-col li{font-size:12.5px;color:var(--muted);line-height:22px;padding:5px 0 6px;border-bottom:1px solid var(--line)}
.footer-bar{position:absolute;left:0;top:3168px;width:1200px;height:70px;background:var(--footer-bar);color:#9a9a9a;font-size:10px;display:flex;align-items:center;justify-content:center}
</style>
</head>
<body>
<div class="page">

  <header class="site-header">
    <div class="brand"><span class="brand-mark"></span><span class="brand-name">Tallowcrest Care</span></div>
    <nav class="main-nav">
      <a href="#">HOME</a><a href="#">ABOUT US</a><a href="#" class="active">WHAT WE DO ⌄</a><a href="#">REFERRALS</a><a href="#">FEEDBACK</a><a href="#">CONTACT US</a>
    </nav>
  </header>

  <section class="hero">
    <div class="hero-photo" role="img" aria-label="Photo of a woman in a wheelchair working on a laptop at a kitchen bench"></div>
    <svg class="hero-shape" width="1200" height="486" viewBox="0 0 1200 486"><polygon points="0,0 365,0 635,486 0,486" fill="#f9b45a" fill-opacity=".93"/></svg>
    <h1 class="hero-title">Vacancies</h1>
    <p class="hero-sub">We can help you find your<br>next home.</p>
  </section>

  <div class="teal-band"></div>

  <form class="search-panel">
    <div class="search-field" style="left:30px;width:222px"><label>CURRENT OR FUTURE</label><div class="select">Both<svg width="6" height="12"><path d="M0 4l3-3 3 3M0 8l3 3 3-3" fill="none" stroke="#aaa"/></svg></div></div>
    <div class="search-field" style="left:275px;width:223px"><label>DESIGN CATEGORY</label><div class="select">All Categories<svg width="6" height="12"><path d="M0 4l3-3 3 3M0 8l3 3 3-3" fill="none" stroke="#aaa"/></svg></div></div>
    <div class="search-field" style="left:518px;width:223px"><label>LOCATION</label><div class="select">All Suburbs<svg width="6" height="12"><path d="M0 4l3-3 3 3M0 8l3 3 3-3" fill="none" stroke="#aaa"/></svg></div></div>
    <div class="go-btn">Go!</div>
  </form>

  <div class="map" role="img" aria-label="Map of Sydney suburbs with pink markers at each property location"></div>

  <p class="eyebrow">PROPERTIES</p>
  <h2 class="section-title">View Our Vacancies &amp;<br>Homes Being Built</h2>

  <div class="listing-grid">
    <article class="property-card">
      <div class="card-photo" role="img" aria-label="Photo of the Greystanes townhouse exterior"><span class="fav"></span><span class="featured">FEATURED</span><span class="gallery"><svg width="11" height="9"><rect x="0.5" y="0.5" width="10" height="8" fill="none" stroke="#222"/><circle cx="5.5" cy="4.5" r="2" fill="#222"/></svg></span><span class="gallery-count">10</span></div>
      <div class="card-body"><span class="status">ALMOST FULL – APPLY NOW!</span><h3 class="card-title">SDA in Greystanes</h3><p class="card-loc"><svg width="7" height="9"><path d="M3.5 0a3.5 3.5 0 0 1 3.5 3.5C7 6 3.5 9 3.5 9S0 6 0 3.5A3.5 3.5 0 0 1 3.5 0z" fill="#999"/></svg>Greystanes</p><p class="card-spec">FULLY ACCESSIBLE, HIGH PHYSICAL SUPPORT</p><span class="details-btn">View Details</span></div>
    </article>
    <article class="property-card is-active">
      <div class="card-photo" role="img" aria-label="Photo of the Jordan Springs home with double garage"><span class="fav"></span><span class="featured">FEATURED</span><span class="slide-arrow prev"></span><span class="slide-arrow next"></span><span class="gallery"><svg width="11" height="9"><rect x="0.5" y="0.5" width="10" height="8" fill="none" stroke="#222"/><circle cx="5.5" cy="4.5" r="2" fill="#222"/></svg></span><span class="gallery-count">10</span></div>
      <div class="card-body"><span class="status">ALMOST FULL – APPLY NOW!</span><h3 class="card-title">SDA in Jordan Springs</h3><p class="card-loc"><svg width="7" height="9"><path d="M3.5 0a3.5 3.5 0 0 1 3.5 3.5C7 6 3.5 9 3.5 9S0 6 0 3.5A3.5 3.5 0 0 1 3.5 0z" fill="#999"/></svg>Jordan Springs</p><p class="card-spec">FULLY ACCESSIBLE, IMPROVED LIVEABILITY</p><span class="details-btn">View Details</span></div>
    </article>
    <article class="property-card">
      <div class="card-photo" role="img" aria-label="Photo of the Werrington townhouse exterior"><span class="fav"></span><span class="featured">FEATURED</span><span class="gallery"><svg width="11" height="9"><rect x="0.5" y="0.5" width="10" height="8" fill="none" stroke="#222"/><circle cx="5.5" cy="4.5" r="2" fill="#222"/></svg></span><span class="gallery-count">10</span></div>
      <div class="card-body"><span class="status">ALMOST FULL – APPLY NOW!</span><h3 class="card-title">SDA in Werrington</h3><p class="card-loc"><svg width="7" height="9"><path d="M3.5 0a3.5 3.5 0 0 1 3.5 3.5C7 6 3.5 9 3.5 9S0 6 0 3.5A3.5 3.5 0 0 1 3.5 0z" fill="#999"/></svg>Werrington</p><p class="card-spec">FULLY ACCESSIBLE, IMPROVED LIVEABILITY</p><span class="details-btn">View Details</span></div>
    </article>

    <article class="property-card">
      <div class="card-photo cloudy" role="img" aria-label="Photo of the Wentworthville brick villas"><span class="fav"></span><span class="featured">FEATURED</span><span class="gallery"><svg width="11" height="9"><rect x="0.5" y="0.5" width="10" height="8" fill="none" stroke="#222"/><circle cx="5.5" cy="4.5" r="2" fill="#222"/></svg></span><span class="gallery-count">10</span></div>
      <div class="card-body"><span class="status">ALMOST FULL – APPLY NOW!</span><h3 class="card-title">SDA villas in Wentworthville</h3><p class="card-loc"><svg width="7" height="9"><path d="M3.5 0a3.5 3.5 0 0 1 3.5 3.5C7 6 3.5 9 3.5 9S0 6 0 3.5A3.5 3.5 0 0 1 3.5 0z" fill="#999"/></svg>Wentworthville</p><p class="card-spec two-line">FULLY ACCESSIBLE, HIGH PHYSICAL SUPPORT, IMPROVED LIVEABILITY</p><span class="details-btn">View Details</span></div>
    </article>
    <article class="property-card">
      <div class="card-photo" role="img" aria-label="Photo of the West Pennant Hills townhouses"><span class="fav"></span><span class="featured">FEATURED</span><span class="gallery"><svg width="11" height="9"><rect x="0.5" y="0.5" width="10" height="8" fill="none" stroke="#222"/><circle cx="5.5" cy="4.5" r="2" fill="#222"/></svg></span><span class="gallery-count">10</span></div>
      <div class="card-body"><span class="status">ALMOST FULL – APPLY NOW!</span><h3 class="card-title">SDA in West Pennant Hills</h3><p class="card-loc"><svg width="7" height="9"><path d="M3.5 0a3.5 3.5 0 0 1 3.5 3.5C7 6 3.5 9 3.5 9S0 6 0 3.5A3.5 3.5 0 0 1 3.5 0z" fill="#999"/></svg>West Pennant Hills</p><p class="card-spec">HIGH PHYSICAL SUPPORT</p><span class="details-btn">View Details</span></div>
    </article>
    <article class="property-card">
      <div class="card-photo" role="img" aria-label="Photo of the Guildford West townhouse exterior"><span class="fav"></span><span class="featured">FEATURED</span><span class="gallery"><svg width="11" height="9"><rect x="0.5" y="0.5" width="10" height="8" fill="none" stroke="#222"/><circle cx="5.5" cy="4.5" r="2" fill="#222"/></svg></span><span class="gallery-count">10</span></div>
      <div class="card-body"><span class="status">ALMOST FULL – APPLY NOW!</span><h3 class="card-title">SDA in Guildford West</h3><p class="card-loc"><svg width="7" height="9"><path d="M3.5 0a3.5 3.5 0 0 1 3.5 3.5C7 6 3.5 9 3.5 9S0 6 0 3.5A3.5 3.5 0 0 1 3.5 0z" fill="#999"/></svg>Guildford West</p><p class="card-spec">FULLY ACCESSIBLE, HIGH PHYSICAL SUPPORT</p><span class="details-btn">View Details</span></div>
    </article>

    <article class="property-card">
      <div class="card-photo interior" role="img" aria-label="Photo of the Austral kitchen interior"><span class="fav"></span><span class="featured">FEATURED</span><span class="gallery"><svg width="11" height="9"><rect x="0.5" y="0.5" width="10" height="8" fill="none" stroke="#222"/><circle cx="5.5" cy="4.5" r="2" fill="#222"/></svg></span><span class="gallery-count">10</span></div>
      <div class="card-body"><span class="status">ALMOST FULL – APPLY NOW!</span><h3 class="card-title">SDA in Austral</h3><p class="card-loc"><svg width="7" height="9"><path d="M3.5 0a3.5 3.5 0 0 1 3.5 3.5C7 6 3.5 9 3.5 9S0 6 0 3.5A3.5 3.5 0 0 1 3.5 0z" fill="#999"/></svg>Austral</p><p class="card-spec two-line">FULLY ACCESSIBLE, HIGH PHYSICAL SUPPORT, ROBUST</p><span class="details-btn">View Details</span></div>
    </article>
    <article class="property-card">
      <div class="card-photo" role="img" aria-label="Photo of the Merrylands brick townhouses"><span class="fav"></span><span class="featured">FEATURED</span><span class="gallery"><svg width="11" height="9"><rect x="0.5" y="0.5" width="10" height="8" fill="none" stroke="#222"/><circle cx="5.5" cy="4.5" r="2" fill="#222"/></svg></span><span class="gallery-count">10</span></div>
      <div class="card-body"><span class="status">ALMOST FULL – APPLY NOW!</span><h3 class="card-title">SDA in Merrylands</h3><p class="card-loc"><svg width="7" height="9"><path d="M3.5 0a3.5 3.5 0 0 1 3.5 3.5C7 6 3.5 9 3.5 9S0 6 0 3.5A3.5 3.5 0 0 1 3.5 0z" fill="#999"/></svg>Merrylands</p><p class="card-spec">FULLY ACCESSIBLE, HIGH PHYSICAL SUPPORT</p><span class="details-btn">View Details</span></div>
    </article>
    <article class="property-card">
      <div class="card-photo cloudy" role="img" aria-label="Photo of the Blacktown home with garage"><span class="fav"></span><span class="featured">FEATURED</span><span class="gallery"><svg width="11" height="9"><rect x="0.5" y="0.5" width="10" height="8" fill="none" stroke="#222"/><circle cx="5.5" cy="4.5" r="2" fill="#222"/></svg></span><span class="gallery-count">10</span></div>
      <div class="card-body"><span class="status">ALMOST FULL – APPLY NOW!</span><h3 class="card-title">SDA in Blacktown</h3><p class="card-loc"><svg width="7" height="9"><path d="M3.5 0a3.5 3.5 0 0 1 3.5 3.5C7 6 3.5 9 3.5 9S0 6 0 3.5A3.5 3.5 0 0 1 3.5 0z" fill="#999"/></svg>Blacktown</p><p class="card-spec">FULLY ACCESSIBLE, IMPROVED LIVEABILITY</p><span class="details-btn">View Details</span></div>
    </article>
  </div>

  <footer class="site-footer">
    <div class="footer-brand"><span class="brand-mark"></span><span class="brand-name">Tallowcrest Care</span></div>
    <ul class="contact-list">
      <li><svg width="14" height="11"><rect x="1" y="1" width="12" height="9" fill="none" stroke="#f08a9a" stroke-width="1.3"/><path d="M1 1l6 5 6-5" fill="none" stroke="#f08a9a" stroke-width="1.3"/></svg>Email: info@tallowcrestcare.com.au</li>
      <li><svg width="14" height="13"><path d="M3 1l3 3-2 2c1 2 2 3 4 4l2-2 3 3-2 2C6 12 1 7 1 3z" fill="#f08a9a"/></svg>Phone: +61 0400 318 562</li>
      <li><svg width="14" height="14"><circle cx="7" cy="7" r="5.5" fill="none" stroke="#f08a9a" stroke-width="1.3"/><path d="M7 4v3.5l2 1.5" fill="none" stroke="#f08a9a" stroke-width="1.3"/></svg>Operating Hours: 9AM To 5PM Monday - Friday</li>
    </ul>
    <div class="social"><span class="badge"></span><span></span><span class="dark"></span><span class="blue"></span></div>
    <div class="footer-col" style="left:612px">
      <h3>ACCOMMODATION</h3>
      <ul><li>Supported Independent Living (SIL)</li><li>Specialist Disability<br>Accommodation (SDA)</li><li>Short term Accommodation<br>(Respite)</li><li>Vacancies</li></ul>
    </div>
    <div class="footer-col" style="left:872px">
      <h3>WHAT WE DO</h3>
      <ul><li>In Home Care</li><li>Social &amp; Community Services</li><li>Therapeutic Supports</li><li>Support Coordination</li><li>Home Modifications</li></ul>
    </div>
  </footer>
  <div class="footer-bar">© Copyright 2021 | Tallowcrest Care | All Rights Reserved.</div>

</div>
</body>
</html>
```